Create a business promotion flyer to leave in customer mailboxes. We are a bulk petroleum supplier, servicing any industry that requires diesel. Base in griffith NSW, servicing griffith area and surrounds.

Business Name - Terra Diesel
Fuel@terradiesel-example.com.au
Owen - 0491 570 362 ohartley@terradiesel-example.com.au
Liam - 0491 570 718 lprosser@terradiesel-example.com.au
Simon - 0491 570 905 skenway@terradiesel-example.com.au
Office 02 5550 1734

Bulk Fuel deliveries.
Oils & lubricants
Local Family owned business

```html
<!DOCTYPE html>
<html lang="en">
<head>
<meta charset="utf-8">
<title>Terra Diesel – Bulk Fuel Flyer</title>
<link href="https://fonts.googleapis.com/css2?family=Poppins:wght@400;500;600;700;800&display=swap" rel="stylesheet">
<style>
:root{
  --red:#ed1c24;
  --charcoal:#414042;
  --ink:#231f20;
  --mist:#e6e7e8;
  --backdrop:#58595b;
  --white:#ffffff;
}
*{margin:0;padding:0;box-sizing:border-box}
html,body{width:1051px;height:1200px;overflow:hidden;background:var(--backdrop);font-family:"Poppins",sans-serif}
.flyer{position:absolute;left:174px;top:154px;width:702px;height:909px;background:var(--white);overflow:hidden}

.hero{position:absolute;left:0;top:0;width:702px;height:426px}
.hero-photo{position:absolute;inset:0;background:
  linear-gradient(180deg,#9fb5d6 0%,#dfe6f0 32%,#b9c0c9 45%,#8d949c 58%,#d9dadb 72%,#ebebea 100%)}
.brand{position:absolute;left:56px;top:64px;font-size:31px;font-weight:600;color:var(--red);letter-spacing:-0.5px}
.tagline-box{position:absolute;left:510px;top:0;width:166px;height:200px;background:var(--red);color:var(--white);
  display:flex;align-items:center;justify-content:center;text-align:center;font-size:17px;line-height:1.3;font-weight:400}
.tagline-box strong{font-weight:700}
.headline{position:absolute;left:56px;top:318px;font-size:43px;font-weight:700;line-height:48px;color:var(--ink);letter-spacing:-1px}
.headline .accent{color:var(--red)}

.services{position:absolute;left:0;top:426px;width:702px;height:219px;display:flex}
.service{height:100%;text-align:center;color:var(--white);padding-top:28px}
.service--dark{background:var(--charcoal)}
.service--red{background:var(--red)}
.service:nth-child(1){width:225px}
.service:nth-child(2){width:242px}
.service:nth-child(3){width:235px}
.service-icon{width:61px;height:61px;border-radius:50%;margin:0 auto;display:flex;align-items:center;justify-content:center}
.service--dark .service-icon{background:var(--red)}
.service--red .service-icon{background:var(--charcoal)}
.service-title{margin-top:12px;font-size:21px;font-weight:700;line-height:25px;letter-spacing:-0.3px}
.service-text{margin-top:5px;font-size:12.5px;line-height:14.5px;font-weight:400}

.contact{position:absolute;left:0;top:645px;width:702px;height:204px;background:var(--mist)}
.contact-lead{position:absolute;left:47px;top:34px;color:var(--ink)}
.contact-lead .lead-red{font-size:27px;font-weight:600;color:var(--red);line-height:35px}
.contact-lead .lead-dark{font-size:27px;font-weight:600;line-height:35px}
.contact-lead .lead-small{font-size:14px;font-weight:500;margin-top:4px}
.person{position:absolute;color:var(--ink)}
.person--left{left:262px}
.person--right{left:476px}
.person .row{display:flex;align-items:center;gap:7px;white-space:nowrap}
.person .name{font-size:17px;font-weight:500;line-height:21px}
.person .phone{font-size:17px;font-weight:600;line-height:21px}
.person .mail{font-size:9.5px;font-weight:400;line-height:17px}
.person svg{flex:none;width:10px;height:10px}

.footer{position:absolute;left:0;top:849px;width:702px;height:60px;background:var(--red);display:flex;align-items:center;justify-content:center;gap:10px;color:var(--white)}
.footer-label{font-size:15px;font-weight:400}
.footer-icon{width:26px;height:26px;border-radius:50%;background:var(--ink);display:flex;align-items:center;justify-content:center}
.footer-mail{font-size:15px;font-weight:700}
</style>
</head>
<body>
<div class="flyer">
  <section class="hero">
    <div class="hero-photo" role="img" aria-label="Photo of a fuel tanker road train parked outside a large steel depot shed under a blue cloudy sky"></div>
    <div class="brand">Terra Diesel</div>
    <div class="tagline-box"><p>Reliable bulk<br>fuel supply<br>across <strong>Griffith</strong><br>and surrounds</p></div>
    <h1 class="headline"><span class="accent">FUEL FOR</span> FARMING,<br>TRANSPORT &amp; INDUSTRY</h1>
  </section>

  <section class="services">
    <div class="service service--dark">
      <div class="service-icon">
        <svg width="34" height="34" viewBox="0 0 34 34" fill="none" stroke="#fff" stroke-width="1.4"><rect x="7" y="4" width="15" height="25" rx="1"/><rect x="10" y="7" width="9" height="5"/><path d="M14.5 15c-2 3-3 4-3 5.5a3 3 0 0 0 6 0c0-1.5-1-2.5-3-5.5z"/><path d="M22 12h3l2 3v11a2 2 0 0 1-4 0v-6h-1"/><path d="M5 29h19"/></svg>
      </div>
      <h2 class="service-title">Bulk Fuel<br>deliveries.</h2>
      <p class="service-text">Reliable diesel supply<br>for any industry.</p>
    </div>
    <div class="service service--red">
      <div class="service-icon">
        <svg width="34" height="34" viewBox="0 0 34 34" fill="none" stroke="#fff" stroke-width="1.4"><path d="M11 9h15a2 2 0 0 1 2 2v17a2 2 0 0 1-2 2H9a2 2 0 0 1-2-2V14z"/><path d="M6 5l4 4M8 3l4 4M6 5l2-2"/><path d="M14 17c-1.5 2.2-2 3-2 4a2 2 0 0 0 4 0c0-1-.5-1.8-2-4z"/><rect x="19" y="16" width="3" height="6" rx="1.5"/><path d="M9 25h17M9 27h17"/></svg>
      </div>
      <h2 class="service-title">Oils &amp;<br>lubricants</h2>
      <p class="service-text">Quality products to keep<br>your equipment<br>performing at its best.</p>
    </div>
    <div class="service service--dark">
      <div class="service-icon">
        <svg width="36" height="34" viewBox="0 0 36 34" fill="none" stroke="#fff" stroke-width="1.5"><circle cx="9" cy="11" r="3.5"/><circle cx="18" cy="14" r="3.5"/><circle cx="27" cy="11" r="3.5"/><path d="M3 24v-2a5 5 0 0 1 9-3"/><path d="M33 24v-2a5 5 0 0 0-9-3"/><path d="M11 27v-2a7 7 0 0 1 14 0v2"/></svg>
      </div>
      <h2 class="service-title">Local Family<br>owned business</h2>
      <p class="service-text">Proudly supporting our<br>local community.</p>
    </div>
  </section>

  <section class="contact">
    <div class="contact-lead">
      <p class="lead-red">Need fuel</p>
      <p class="lead-dark">for your<br>operation?</p>
      <p class="lead-small">Contact Us</p>
    </div>

    <div class="person person--left" style="top:32px">
      <div class="row name"><svg viewBox="0 0 10 10"><circle cx="5" cy="3" r="2.2" fill="#ed1c24"/><path d="M1 10a4 3.5 0 0 1 8 0z" fill="#ed1c24"/></svg>Owen</div>
      <div class="row phone"><svg viewBox="0 0 10 10"><path d="M3 1L1.5 2.5c0 4 2 6 6 6L9 7 7 5.5 6 6.5c-1 0-2.5-1.5-2.5-2.5l1-1z" fill="#ed1c24"/></svg>0491 570 362</div>
      <div class="row mail"><svg viewBox="0 0 10 10"><rect x="1" y="2.5" width="8" height="5" fill="#ed1c24"/><path d="M1 2.5l4 3 4-3" stroke="#fff" stroke-width=".8" fill="none"/></svg>ohartley@terradiesel-example.com.au</div>
    </div>

    <div class="person person--left" style="top:118px">
      <div class="row name"><svg viewBox="0 0 10 10"><circle cx="5" cy="3" r="2.2" fill="#ed1c24"/><path d="M1 10a4 3.5 0 0 1 8 0z" fill="#ed1c24"/></svg>Simon</div>
      <div class="row phone"><svg viewBox="0 0 10 10"><path d="M3 1L1.5 2.5c0 4 2 6 6 6L9 7 7 5.5 6 6.5c-1 0-2.5-1.5-2.5-2.5l1-1z" fill="#ed1c24"/></svg>0491 570 905</div>
      <div class="row mail"><svg viewBox="0 0 10 10"><rect x="1" y="2.5" width="8" height="5" fill="#ed1c24"/><path d="M1 2.5l4 3 4-3" stroke="#fff" stroke-width=".8" fill="none"/></svg>skenway@terradiesel-example.com.au</div>
    </div>

    <div class="person person--right" style="top:34px">
      <div class="row name"><svg viewBox="0 0 10 10"><circle cx="5" cy="3" r="2.2" fill="#ed1c24"/><path d="M1 10a4 3.5 0 0 1 8 0z" fill="#ed1c24"/></svg>Liam</div>
      <div class="row phone"><svg viewBox="0 0 10 10"><path d="M3 1L1.5 2.5c0 4 2 6 6 6L9 7 7 5.5 6 6.5c-1 0-2.5-1.5-2.5-2.5l1-1z" fill="#ed1c24"/></svg>0491 570 718</div>
      <div class="row mail"><svg viewBox="0 0 10 10"><rect x="1" y="2.5" width="8" height="5" fill="#ed1c24"/><path d="M1 2.5l4 3 4-3" stroke="#fff" stroke-width=".8" fill="none"/></svg>lprosser@terradiesel-example.com.au</div>
    </div>

    <div class="person person--right" style="top:130px">
      <div class="row name"><svg viewBox="0 0 10 10" fill="none" stroke="#ed1c24" stroke-width=".8"><rect x="1" y="4" width="4" height="5.5"/><rect x="5" y="1" width="4" height="8.5"/></svg>Office</div>
      <div class="row phone"><svg viewBox="0 0 10 10"><path d="M3 1L1.5 2.5c0 4 2 6 6 6L9 7 7 5.5 6 6.5c-1 0-2.5-1.5-2.5-2.5l1-1z" fill="#ed1c24"/></svg>02 5550 1734</div>
    </div>
  </section>

  <footer class="footer">
    <span class="footer-label">Have questions? Email us at:</span>
    <span class="footer-icon"><svg width="13" height="10" viewBox="0 0 13 10"><rect x="0.5" y="0.5" width="12" height="9" fill="#fff"/><path d="M0.5 0.5l6 5 6-5" stroke="#231f20" fill="none"/></svg></span>
    <span class="footer-mail">Fuel@terradiesel-example.com.au</span>
  </footer>
</div>
</body>
</html>
```